The design should look similar to the uploaded example to accommodate the information needed for a business card template. I would like to see the colors orange and charcoal grey incorporated along with the logo.The following should be on the back of the card SPECIALIZING IN NEW AND USED TIRES & WHEELS FOR:- Loaders- Skid Steers- Telehandlers- Boom Lifts- Forklifs and moreELIMINATING DOWNTIMEWheel Exchange Program for New & Used Foam Filled and Solid Rubber TiresSPECIALTY SERVICES- Foam Filling Tires- Largest Tire Press in SE- ONSITE Forklift Tire Press- Boom Truck Services - Rubber Tracks

Target Market(s)

New and Existing Customers

Industry/Entity Type

Business

Contact Information for Business Card

NAMEHEAVY DUTY TIRE, LLC8470 Belvedere RoadWest Palm Beach, FL 33411P: 844-HD-TIRESF: 561-431-6469C:E: W: WWW.GRANITERIMSUPPLY-EXAMPLE.COM

Font styles to use
Sans Serif

Colors
f37122
333333

Requirements
Must have
• The logo and the information indicated for the backside of the card
Nice to have
• Keep the orange and charcoal grey colors

```html
<!DOCTYPE html>
<html lang="en">
<head>
<meta charset="utf-8">
<title>Granite Rim Supply – Business Card</title>
<link rel="stylesheet" href="https://fonts.googleapis.com/css2?family=Open+Sans:wght@400;600;700&display=swap">
<style>
  :root {
    --orange: #f37122;
    --orange-soft: #f7883f;
    --charcoal: #333333;
    --charcoal-line: #3d4346;
    --white: #ffffff;
    --paper: #f4f4f4;
    --backdrop: #e6e2dc;
  }
  * { box-sizing: border-box; margin: 0; padding: 0; }
  html, body {
    width: 1200px; height: 900px; overflow: hidden;
    background: var(--backdrop);
    font-family: "Open Sans", Arial, sans-serif;
  }
  .canvas { position: relative; width: 1200px; height: 900px; }

  .card {
    position: absolute; width: 560px; height: 320px;
    background: var(--white); overflow: hidden;
    box-shadow: 0 6px 18px rgba(0,0,0,.18);
  }
  .card--back { left: 80px; top: 110px; }
  .card--front { left: 560px; top: 470px; }

  .card__top { position: absolute; left: 0; right: 0; top: 0; background: linear-gradient(#fff, var(--paper)); }
  .card__rule { position: absolute; left: 0; right: 0; height: 9px; background: var(--charcoal-line); }
  .card__bottom { position: absolute; left: 0; right: 0; bottom: 0; background: var(--orange-soft); color: var(--white); }

  .card--back .card__top { height: 142px; }
  .card--back .card__rule { top: 142px; }
  .card--back .card__bottom { top: 151px; }

  .brand { display: flex; align-items: center; gap: 8px; }
  .brand__dot { width: 16px; height: 16px; border-radius: 50%; background: var(--orange); flex: none; }
  .brand__name { font-weight: 700; color: var(--charcoal); letter-spacing: .5px; white-space: nowrap; }

  .card--back .brand { position: absolute; left: 22px; top: 56px; }
  .card--back .brand__name { font-size: 19px; }

  .pitch { position: absolute; left: 208px; top: 40px; width: 340px; }
  .pitch__kicker { color: var(--orange); font-weight: 600; font-size: 14px; letter-spacing: .2px; }
  .pitch__text { color: var(--charcoal); font-weight: 600; font-size: 14.5px; line-height: 1.25; white-space: nowrap; }

  .services { position: absolute; left: 20px; top: 16px; width: 250px; text-align: right; }
  .services__title { font-size: 18px; font-weight: 600; letter-spacing: .3px; margin-bottom: 6px; }
  .services__list { list-style: none; font-size: 14px; line-height: 1.45; }
  .services__list li::after {
    content: ""; display: inline-block; width: 6px; height: 6px; border-radius: 50%;
    background: var(--white); margin-left: 8px; vertical-align: middle;
  }

  .equipment { position: absolute; left: 292px; top: 14px; width: 250px; }
  .equipment__title { font-size: 13.5px; font-weight: 600; line-height: 1.2; letter-spacing: .2px; margin-bottom: 8px; }
  .equipment__list { list-style: none; font-size: 13px; line-height: 1.45; }
  .equipment__list li::before {
    content: ""; display: inline-block; width: 6px; height: 6px; border-radius: 50%;
    background: var(--white); margin-right: 7px; vertical-align: middle;
  }

  .card--front .card__top { height: 166px; }
  .card--front .card__rule { top: 166px; }
  .card--front .card__bottom { top: 175px; }
  .card--front .brand { position: absolute; left: 0; right: 0; top: 70px; justify-content: center; }
  .card--front .brand__name { font-size: 24px; }

  .contact { position: absolute; left: 20px; top: 12px; width: 290px; text-align: right; list-style: none; font-size: 14.5px; line-height: 1.6; }
  .contact li { display: flex; justify-content: flex-end; align-items: center; gap: 8px; white-space: nowrap; }
  .contact svg { width: 13px; height: 13px; flex: none; }

  .person { position: absolute; left: 326px; top: 10px; width: 220px; }
  .person__name { font-size: 17px; font-weight: 600; margin-bottom: 6px; }
  .person__company { font-size: 13.5px; font-weight: 600; margin-bottom: 4px; }
  .person__address { font-style: normal; font-size: 13px; line-height: 1.4; }
</style>
</head>
<body>
<main class="canvas">

  <section class="card card--back" aria-label="Business card back">
    <div class="card__top">
      <div class="brand"><span class="brand__dot"></span><span class="brand__name">GRANITE RIM</span></div>
      <div class="pitch">
        <p class="pitch__kicker">ELIMINATING DOWNTIME</p>
        <p class="pitch__text">Wheel Exchange Program for New &amp;<br>Used Foam Filled and Solid Rubber Tires</p>
      </div>
    </div>
    <div class="card__rule"></div>
    <div class="card__bottom">
      <div class="services">
        <h2 class="services__title">SPECIALTY SERVICES</h2>
        <ul class="services__list">
          <li>Foam Filling Tires</li>
          <li>Largest Tire Press in SE</li>
          <li>ONSITE Forklift Tire Press</li>
          <li>Boom Truck Services</li>
          <li>Rubber Tracks</li>
        </ul>
      </div>
      <div class="equipment">
        <h2 class="equipment__title">SPECIALIZING IN NEW AND<br>USED TIRES &amp; WHEELS FOR:</h2>
        <ul class="equipment__list">
          <li>Loaders</li>
          <li>Skid Steers</li>
          <li>Telehandlers Boom Lifts</li>
          <li>Forklifs and more</li>
        </ul>
      </div>
    </div>
  </section>

  <section class="card card--front" aria-label="Business card front">
    <div class="card__top">
      <div class="brand"><span class="brand__dot"></span><span class="brand__name">GRANITE RIM</span></div>
    </div>
    <div class="card__rule"></div>
    <div class="card__bottom">
      <ul class="contact">
        <li>844-GR-WHEEL
          <svg viewBox="0 0 16 16" aria-hidden="true"><path fill="#fff" d="M3.6 1.5l2.3 2.6-1.3 1.6c.9 2 2.6 3.7 4.6 4.6l1.6-1.3 2.6 2.3-1.4 2.2C7 13.2 2.8 9 1.5 3z"/></svg></li>
        <li>561-278-9053
          <svg viewBox="0 0 16 16" aria-hidden="true"><rect x="4" y="1" width="8" height="5" fill="#fff"/><rect x="1" y="6" width="14" height="8" rx="1" fill="#fff"/><rect x="4" y="9" width="8" height="1.5" fill="#f7883f"/></svg></li>
        <li>123-456-7890
          <svg viewBox="0 0 16 16" aria-hidden="true"><rect x="4" y="1" width="8" height="14" rx="1.5" fill="none" stroke="#fff" stroke-width="1.6"/><circle cx="8" cy="12.5" r="1" fill="#fff"/></svg></li>
        <li>info@graniterim-example.com
          <svg viewBox="0 0 16 16" aria-hidden="true"><rect x="1" y="3" width="14" height="10" fill="#fff"/><path d="M1 3l7 6 7-6" fill="none" stroke="#f7883f" stroke-width="1.3"/></svg></li>
        <li>www.graniterimsupply-example.com
          <svg viewBox="0 0 16 16" aria-hidden="true"><circle cx="8" cy="8" r="6.5" fill="none" stroke="#fff" stroke-width="1.4"/><ellipse cx="8" cy="8" rx="2.6" ry="6.5" fill="none" stroke="#fff" stroke-width="1.1"/><path d="M1.5 8h13" stroke="#fff" stroke-width="1.1"/></svg></li>
      </ul>
      <div class="person">
        <p class="person__name">Marcus Hale</p>
        <p class="person__company">GRANITE RIM SUPPLY, LLC</p>
        <address class="person__address">5126 Marston Lane<br>Lake Corvina, FL 33490</address>
      </div>
    </div>
  </section>

</main>
</body>
</html>
```